QVR business card

Need a business card for a company that provides instructional design and elearning development services. The website is here: http://quorvane.studio/

I'm attaching a current logo, as well as the old business card design. While I like to keep it clean, the old design is too simplistic for my liking. The only idea I want to reuse from the old design is placing industry jargon on the back of the card, just need a better way to present it. But if you have other ideas for the back--feel free to experiment.

Please use the colors complementary to the color we have on the website. Thank you!

```html
<!DOCTYPE html>
<html lang="en">
<head>
<meta charset="utf-8">
<title>QVR business card</title>
<link rel="stylesheet" href="https://fonts.googleapis.com/css2?family=Arimo:wght@400;700&family=Open+Sans:wght@800&family=PT+Sans+Narrow&display=swap">
<style>
  :root {
    --teal: #14b2ae;
    --teal-dark: #0f9c98;
    --gold: #d9cb93;
    --ink: #2f2f2f;
    --paper: #ffffff;
    --backdrop: #2a2a2a;
    --rule: #b9b9b9;
  }
  * { box-sizing: border-box; margin: 0; padding: 0; }
  html, body {
    width: 1200px; height: 873px; overflow: hidden;
    background: var(--backdrop);
  }
  .stage {
    position: relative; width: 1200px; height: 873px;
    display: flex; align-items: center; justify-content: center; gap: 40px;
  }
  .card {
    position: relative; width: 540px; height: 309px; overflow: hidden;
    box-shadow: 0 10px 30px rgba(0,0,0,.45);
  }

  /* Back of card */
  .card-back { background: var(--teal); color: var(--paper); }
  .card-back .headline {
    position: absolute; left: 24px; top: 36px;
    font-family: "Open Sans", sans-serif; font-weight: 800;
    font-size: 52px; line-height: 1; letter-spacing: 1px;
  }
  .card-back .divider {
    position: absolute; left: 214px; top: 30px; bottom: 30px;
    width: 1px; background: rgba(255,255,255,.75);
  }
  .card-back .jargon {
    position: absolute; left: 230px; right: 14px; top: 52px; list-style: none;
    font-family: "PT Sans Narrow", sans-serif; font-size: 22px;
    line-height: 34px; text-transform: uppercase; letter-spacing: .2px;
    white-space: nowrap;
  }

  /* Front of card */
  .card-front { background: var(--paper); font-family: "Arimo", sans-serif; }
  .card-front .waves { position: absolute; inset: 0; }
  .card-front .brand {
    position: absolute; left: 0; right: 0; top: 52px;
    display: flex; align-items: center; justify-content: center; gap: 12px;
  }
  .card-front .brand-dot {
    width: 26px; height: 26px; border-radius: 50%; background: var(--teal);
  }
  .card-front .brand-name {
    font-family: "Arimo", sans-serif; font-weight: 700; font-size: 52px;
    color: var(--gold); letter-spacing: 2px;
  }
  .card-front .person {
    position: absolute; right: 300px; top: 156px; text-align: right;
  }
  .card-front .person-name {
    color: var(--teal); font-weight: 700; font-size: 17px; letter-spacing: .5px;
  }
  .card-front .person-role { color: var(--ink); font-size: 16px; margin-top: 2px; }
  .card-front .contact-rule {
    position: absolute; left: 252px; top: 136px; width: 1px; height: 72px;
    background: var(--rule);
  }
  .card-front .contacts {
    position: absolute; left: 262px; top: 134px; list-style: none;
    color: var(--ink); font-size: 15px; line-height: 24px; white-space: nowrap;
  }
  .card-front .contacts li { display: flex; align-items: center; gap: 7px; }
  .card-front .contacts svg { width: 15px; height: 15px; flex: none; }
</style>
</head>
<body>
<main class="stage">

  <section class="card card-back" aria-label="Card back">
    <p class="headline">HOW<br>CAN<br>WE<br>HELP?</p>
    <div class="divider"></div>
    <ul class="jargon">
      <li>Mobile Learning SCORM</li>
      <li>Instructional Design LMS</li>
      <li>MOOCs eLearning HTML5</li>
      <li>Adult Learning Theory</li>
      <li>Gamification Classroom</li>
      <li>xAPI Blended Learning</li>
    </ul>
  </section>

  <section class="card card-front" aria-label="Card front">
    <svg class="waves" viewBox="0 0 540 309" preserveAspectRatio="none" aria-hidden="true">
      <path d="M0 252 C150 218 330 236 540 278 L540 309 L0 309 Z" fill="var(--teal)"/>
      <path d="M350 236 C430 220 495 204 540 184 L540 222 C480 232 420 236 350 236 Z" fill="var(--teal)"/>
      <path d="M320 250 C410 246 485 236 540 222 L540 234 C475 248 410 252 320 250 Z" fill="var(--gold)"/>
    </svg>

    <div class="brand">
      <span class="brand-dot"></span>
      <span class="brand-name">QVR</span>
    </div>

    <div class="person">
      <p class="person-name">MARCUS HALVORSEN</p>
      <p class="person-role">Managing Director</p>
    </div>

    <div class="contact-rule"></div>
    <ul class="contacts">
      <li>
        <svg viewBox="0 0 16 16" aria-hidden="true"><path d="M3 6 C3 3 13 3 13 6 L11 7 L10 5.5 L6 5.5 L5 7 Z M4 8 L12 8 L13 13 L3 13 Z" fill="var(--teal)"/></svg>
        555-014-2287
      </li>
      <li>
        <svg viewBox="0 0 16 16" aria-hidden="true"><circle cx="8" cy="8" r="8" fill="var(--teal)"/><rect x="3.5" y="5" width="9" height="6" fill="#fff"/><path d="M3.5 5 L8 8.5 L12.5 5" stroke="var(--teal)" fill="none"/></svg>
        mhalvorsen@quorvane.studio
      </li>
      <li>
        <svg viewBox="0 0 16 16" aria-hidden="true"><circle cx="8" cy="8" r="7" fill="var(--teal)"/><path d="M1 8 H15 M8 1 V15 M8 1 C4 4 4 12 8 15 M8 1 C12 4 12 12 8 15" stroke="#fff" stroke-width=".9" fill="none"/></svg>
        www.quorvane.studio
      </li>
    </ul>
  </section>

</main>
</body>
</html>
```